Business Card for a mobile physiotherapy company

I need a layout for a business card for a mobile physiotherapy company.
Slogan is "Mobile Physiotherapy - Your Road To Recovery"
Phone number is 867-555-0142
Email VardenTherapy@postnest.ca (subject to change with website)
Website www.VardenTherapy.ca
My name and credentials: Luke Varden Luke Varden, BSc(kin), MPT, CAFCI, IMS
Information maybe included: Direct Billing, Services including Physiotherapy, IMS, acupuncture
Maybe include facebook and instagram logos
One side with the logo clean and sharp
Other side with details, try not to look too busy, keep everything concise

```html
<!DOCTYPE html>
<html lang="en">
<head>
<meta charset="utf-8">
<title>Varden Therapy – Business Card</title>
<link rel="stylesheet" href="https://fonts.googleapis.com/css2?family=Roboto:ital,wght@0,400;0,500;0,700;1,400&display=swap">
<style>
  :root {
    --navy: #2c4870;
    --forest: #0b5249;
    --white: #ffffff;
    --backdrop: #e9e7e3;
    --card-shadow: 0 6px 18px rgba(0,0,0,0.28);
  }
  * { box-sizing: border-box; margin: 0; padding: 0; }
  html, body {
    width: 1125px; height: 1200px; overflow: hidden;
    background: var(--backdrop);
    font-family: "Roboto", Arial, sans-serif;
  }
  .canvas { position: relative; width: 1125px; height: 1200px; }
  .card {
    position: absolute; left: 162px; width: 800px; height: 456px;
    box-shadow: var(--card-shadow); overflow: hidden;
  }
  .card--front { top: 110px; background: var(--white); }
  .card--back { top: 634px; background: var(--forest); color: var(--white); }

  .front-panel { position: absolute; inset: 0; }
  .front-details { position: absolute; left: 54px; top: 56px; color: var(--white); }
  .person-name { font-size: 29px; font-weight: 700; letter-spacing: 0.3px; line-height: 1; }
  .credentials { font-size: 19px; font-weight: 400; margin-top: 4px; }
  .billing { font-size: 20px; font-weight: 500; margin-top: 6px; }

  .contact-list {
    position: absolute; left: 54px; top: 326px; list-style: none;
    color: var(--white); font-size: 19px;
  }
  .contact-list li { display: flex; align-items: center; height: 26px; }
  .contact-list svg { width: 18px; height: 18px; margin-right: 12px; fill: var(--white); }

  .brand-front {
    position: absolute; left: 478px; top: 178px; width: 280px;
    text-align: center; color: var(--forest); font-weight: 700;
  }
  .brand-front .brand-main { font-size: 52px; letter-spacing: 3px; line-height: 1; }
  .brand-front .brand-sub { font-size: 25px; letter-spacing: 11px; margin-top: 12px; }

  .social-dots { position: absolute; right: 24px; top: 40px; display: flex; gap: 6px; }
  .social-dots span { width: 36px; height: 36px; border-radius: 50%; background: var(--white); }

  .brand-back { position: absolute; left: 0; right: 0; top: 168px; text-align: center; font-weight: 700; }
  .brand-back .brand-main { font-size: 72px; letter-spacing: 6px; line-height: 1; }
  .brand-back .brand-sub { font-size: 34px; letter-spacing: 17px; margin-top: 20px; padding-left: 17px; }

  .tagline { position: absolute; left: 0; right: 0; top: 362px; text-align: center; font-size: 19px; }
  .tagline .slogan { font-style: italic; }
  .tagline .services { margin-top: 6px; }
</style>
</head>
<body>
<main class="canvas">
  <section class="card card--front">
    <svg class="front-panel" viewBox="0 0 800 456" width="800" height="456" aria-hidden="true">
      <polygon points="0,0 471,0 288,228 471,456 0,456" fill="var(--navy)"/>
    </svg>
    <div class="front-details">
      <h1 class="person-name">LUKE VARDEN</h1>
      <p class="credentials">BSc(kin), MPT, CAFCI, IMS</p>
      <p class="billing">Direct Billing</p>
    </div>
    <ul class="contact-list">
      <li><svg viewBox="0 0 24 24"><path d="M6.6 10.8a15.1 15.1 0 0 0 6.6 6.6l2.2-2.2a1 1 0 0 1 1-.25 11.4 11.4 0 0 0 3.6.57 1 1 0 0 1 1 1V20a1 1 0 0 1-1 1A17 17 0 0 1 3 4a1 1 0 0 1 1-1h3.5a1 1 0 0 1 1 1c0 1.25.2 2.45.57 3.57a1 1 0 0 1-.25 1z"/></svg>867-555-0142</li>
      <li><svg viewBox="0 0 24 24"><path d="M2 5h20v14H2z M4 7v.5l8 5 8-5V7l-8 5z" fill-rule="evenodd"/></svg>VardenTherapy@postnest.ca</li>
      <li><svg viewBox="0 0 24 24"><circle cx="12" cy="12" r="10"/></svg>www.VardenTherapy.ca</li>
    </ul>
    <div class="brand-front">
      <p class="brand-main">VARDEN</p>
      <p class="brand-sub">THERAPY</p>
    </div>
  </section>

  <section class="card card--back">
    <div class="social-dots" aria-label="Social media"><span></span><span></span></div>
    <div class="brand-back">
      <p class="brand-main">VARDEN</p>
      <p class="brand-sub">THERAPY</p>
    </div>
    <div class="tagline">
      <p class="slogan">Mobile Physiotherapy - Your Road To Recovery</p>
      <p class="services">Physiotherapy • IMS • Acupuncture</p>
    </div>
  </section>
</main>
</body>
</html>
```